Business cards to launch an education platform

Hi,
I am looking at having new business cards designed.
I am a startup, developing a web platform for schools and university, the education world. It's an online assessment system.
I would like a card that looks classy, and that is using the colors and the font of my logo.

I have attached:
1) my logo
2) A business card that I have designed quickly so you can have all the information required in the card, but I really don't like it.
3) The font that I am using (Lato Regular) to design my web platform
4) Some screenshots of my web platform so you can have a look at the style that I have.

Target Market(s)

Major market: Education system: Schools and university
Minor markets: Business in general

Industry/Entity Type

Business

Contact Information for Business Card

Clara Fenwick
Director

M: 0437 518 902
E: clara.fenwick@amberLoomSystems.com.au

Requirements
Must have
• The colors of my logo

```html
<!DOCTYPE html>
<html lang="en">
<head>
<meta charset="utf-8">
<title>Amber Loom Systems — Business Cards</title>
<link rel="stylesheet" href="https://fonts.googleapis.com/css2?family=Lato:wght@400;700&display=swap">
<style>
  :root {
    --backdrop: #2f2a27;
    --card: #1b1b1d;
    --card-edge: #262628;
    --brand-blue: #1f8ad9;
    --brand-blue-deep: #1665b0;
    --text-light: #d6d6d6;
    --text-muted: #a9a9ab;
    --divider: #3a4656;
  }
  * { margin: 0; padding: 0; box-sizing: border-box; }
  html, body {
    width: 1200px;
    height: 844px;
    overflow: hidden;
    background: var(--backdrop);
    font-family: "Lato", Arial, sans-serif;
  }
  .card-set {
    position: relative;
    width: 1200px;
    height: 844px;
  }
  .card {
    position: absolute;
    top: 274px;
    width: 520px;
    height: 297px;
    background: var(--card);
    border: 1px solid var(--card-edge);
    border-radius: 3px;
    box-shadow: 0 10px 24px rgba(0,0,0,0.45);
  }
  .card--contact { left: 50px; }
  .card--brand { left: 630px; }

  /* Contact side */
  .brand-mark {
    position: absolute;
    left: 40px;
    top: 98px;
    width: 150px;
    display: flex;
    flex-direction: column;
    align-items: center;
    gap: 12px;
  }
  .brand-mark__square {
    width: 62px;
    height: 62px;
    background: var(--brand-blue);
  }
  .brand-mark__name {
    color: var(--brand-blue);
    font-size: 14px;
    font-weight: 400;
    letter-spacing: 0.5px;
    text-align: center;
  }
  .contact-divider {
    position: absolute;
    left: 212px;
    top: 92px;
    width: 1px;
    height: 118px;
    background: var(--divider);
  }
  .contact {
    position: absolute;
    left: 228px;
    top: 96px;
  }
  .contact__name {
    color: var(--brand-blue);
    font-size: 20px;
    font-weight: 400;
    line-height: 1.1;
  }
  .contact__role {
    color: var(--text-light);
    font-size: 13px;
    margin-top: 2px;
  }
  .contact__list {
    list-style: none;
    margin-top: 22px;
  }
  .contact__item {
    display: flex;
    align-items: center;
    gap: 9px;
    color: var(--text-light);
    font-size: 13.5px;
    line-height: 1.55;
  }
  .contact__icon {
    width: 11px;
    height: 11px;
    flex: none;
  }

  /* Brand side */
  .brand-lockup {
    position: absolute;
    left: 0;
    right: 0;
    top: 0;
    bottom: 0;
    display: flex;
    align-items: center;
    justify-content: center;
    gap: 18px;
  }
  .brand-lockup__square {
    width: 72px;
    height: 72px;
    background: var(--brand-blue);
  }
  .brand-lockup__name {
    color: var(--brand-blue);
    font-size: 30px;
    font-weight: 400;
    letter-spacing: 1.5px;
  }
</style>
</head>
<body>
  <main class="card-set">
    <section class="card card--contact" aria-label="Contact side of business card">
      <div class="brand-mark">
        <div class="brand-mark__square"></div>
        <span class="brand-mark__name">Amber Loom Systems</span>
      </div>
      <div class="contact-divider"></div>
      <div class="contact">
        <h1 class="contact__name">Clara Fenwick</h1>
        <p class="contact__role">Director</p>
        <ul class="contact__list">
          <li class="contact__item">
            <svg class="contact__icon" viewBox="0 0 12 12" aria-hidden="true">
              <path d="M2.5 0.8 L4.3 0.8 L5 3.2 L3.8 4.2 C4.5 5.8 6 7.4 7.8 8.2 L8.8 7 L11.2 7.7 L11.2 9.5 C11.2 10.5 10.4 11.2 9.4 11.1 C4.9 10.6 1.4 7.1 0.9 2.6 C0.8 1.6 1.5 0.8 2.5 0.8 Z" fill="#1f8ad9"/>
            </svg>
            <span>0437 518 902</span>
          </li>
          <li class="contact__item">
            <svg class="contact__icon" viewBox="0 0 12 12" aria-hidden="true">
              <rect x="0.5" y="2" width="11" height="8" rx="1" fill="#1f8ad9"/>
              <path d="M1 2.6 L6 6.4 L11 2.6" fill="none" stroke="#1b1b1d" stroke-width="1"/>
            </svg>
            <span>clara.fenwick@amberLoomSystems.com.au</span>
          </li>
        </ul>
      </div>
    </section>

    <section class="card card--brand" aria-label="Brand side of business card">
      <div class="brand-lockup">
        <div class="brand-lockup__square"></div>
        <span class="brand-lockup__name">Amber Loom Systems</span>
      </div>
    </section>
  </main>
</body>
</html>
```